KORV PTY LTD - Business Cards

Design a modern business card - using the attached Designs.
Same design as on the front, apart from the names/numbers/emails to be different.
We want the cards to be very glossy to stand out, do I think the simple black/white/metallic will be effective.
Both lots of details below:

Tom Wrenshaw
Director
tom_korv@nulvane.com
0438 274 093

Lewis Corbyn
Director
lewis_korv@nulvane.com
0419 385 642

Industry/Entity Type

Business

```html
<!DOCTYPE html>
<html lang="en">
<head>
<meta charset="utf-8">
<title>KORV PTY LTD – Business Cards</title>
<link rel="stylesheet" href="https://fonts.googleapis.com/css2?family=Bitter:wght@400;700&display=swap">
<style>
  :root {
    --stage: #ececec;
    --card-dark-hi: #8a8d90;
    --card-dark-mid: #3a3c3e;
    --card-dark-lo: #121314;
    --card-grey: #b3b3b3;
    --ink-light: #f4f4f4;
    --ink-dark: #2a2b2d;
    --mark-light: #d9dadb;
  }
  * { box-sizing: border-box; margin: 0; padding: 0; }
  html, body {
    width: 1200px;
    height: 456px;
    overflow: hidden;
    background: var(--stage);
  }
  .canvas {
    position: relative;
    width: 1200px;
    height: 456px;
    font-family: "Bitter", Georgia, serif;
  }
  .card {
    position: absolute;
    top: 58px;
    width: 540px;
    height: 340px;
    border-radius: 4px;
    box-shadow: 0 6px 18px rgba(0,0,0,.25);
    overflow: hidden;
  }
  .card--front { left: 40px; }
  .card--back {
    left: 620px;
    background: var(--card-grey);
  }
  .brushed-metal {
    position: absolute;
    inset: 0;
    background:
      radial-gradient(ellipse at 70% 35%, var(--card-dark-hi) 0%, var(--card-dark-mid) 40%, var(--card-dark-lo) 85%);
  }
  .brand {
    position: absolute;
    display: flex;
    align-items: center;
    gap: 12px;
    font-weight: 700;
    letter-spacing: 0.04em;
  }
  .brand__dot {
    border-radius: 50%;
    flex: none;
  }
  .card--front .brand {
    left: 44px;
    top: 210px;
    color: var(--mark-light);
    font-size: 50px;
  }
  .card--front .brand__dot {
    width: 26px; height: 26px;
    background: var(--mark-light);
  }
  .card--back .brand {
    left: 50%;
    top: 50%;
    transform: translate(-50%, -50%);
    color: var(--ink-dark);
    font-size: 92px;
  }
  .card--back .brand__dot {
    width: 44px; height: 44px;
    background: var(--ink-dark);
  }
  .contact {
    position: absolute;
    left: 300px;
    top: 120px;
    color: var(--ink-light);
  }
  .contact__name {
    font-size: 20px;
    font-weight: 400;
    letter-spacing: 0.01em;
  }
  .contact__role {
    font-size: 13px;
    margin-top: 4px;
  }
  .contact__lines {
    list-style: none;
    margin-top: 36px;
    font-size: 14px;
    line-height: 1.6;
  }
  .contact__lines li {
    display: flex;
    align-items: center;
    gap: 7px;
  }
  .contact__lines svg {
    width: 12px;
    height: 12px;
    fill: var(--ink-light);
    flex: none;
  }
</style>
</head>
<body>
<main class="canvas">

  <section class="card card--front" aria-label="Business card front">
    <div class="brushed-metal" role="img" aria-label="Brushed metal texture background"></div>

    <div class="brand">
      <span class="brand__dot"></span>
      <span class="brand__name">KORV</span>
    </div>

    <div class="contact">
      <h1 class="contact__name">Lewis Corbyn</h1>
      <p class="contact__role">Director</p>
      <ul class="contact__lines">
        <li>
          <svg viewBox="0 0 24 24" aria-hidden="true"><path d="M6.6 10.8a15.1 15.1 0 0 0 6.6 6.6l2.2-2.2a1 1 0 0 1 1-.25 11.4 11.4 0 0 0 3.6.57 1 1 0 0 1 1 1V20a1 1 0 0 1-1 1A17 17 0 0 1 3 4a1 1 0 0 1 1-1h3.5a1 1 0 0 1 1 1c0 1.25.2 2.45.57 3.57a1 1 0 0 1-.25 1z"/></svg>
          <span>0419 385 642</span>
        </li>
        <li>
          <svg viewBox="0 0 24 24" aria-hidden="true"><path d="M2 9l10-6 10 6v11H2z M4 10v8h16v-8l-8 5z"/></svg>
          <span>lewis_korv@nulvane.com</span>
        </li>
      </ul>
    </div>
  </section>

  <section class="card card--back" aria-label="Business card back">
    <div class="brand">
      <span class="brand__dot"></span>
      <span class="brand__name">KORV</span>
    </div>
  </section>

</main>
</body>
</html>
```